Bed Company needs business card

Hello, we are a bed company that makes specialized magnets for beds. We are an alternative healing company. I need a modern and upscale business card. Please incorporate my logo for the card.

Accepted file formats are AI, EPS, and Press-Ready PDFS.

Please include all fonts or convert them to outlines regardless of file type.

If you are designing the card in Photoshop the file Must be 1200dpi.

I am open to anything for the business card.  I really like all of your designs and if you want to change the color of the logo, you can.  I will be making the final selection by Friday.  Thank You for all of your designs.  Feel Free to submit different color logos if you want.  

Reason: I will make a decision Final on Friday April 20th. 2012. Good Luck and Thank you all for the designs.

Target Market(s)

My target Market is people, who are looking for alternative healing.

Industry/Entity Type

Business

Requirements
Must have
• My logo must be incorporated. The front card must have

Name
Job Title

Address
Work
Cell
Fax
email
web

Just put in fake info for the card.

The back of the card. I want the logo on the back with color. I just want it to look modern and cool.

```html
<!DOCTYPE html>
<html lang="en">
<head>
<meta charset="utf-8">
<title>Restwave – Business Card</title>
<link href="https://fonts.googleapis.com/css2?family=Open+Sans:wght@400;600;700&display=swap" rel="stylesheet">
<style>
  :root {
    --canvas: #ececec;
    --paper: #ffffff;
    --green: #55b948;
    --green-dark: #0f6434;
    --ink: #333333;
    --ink-soft: #555555;
  }
  * { box-sizing: border-box; margin: 0; padding: 0; }
  html, body {
    width: 794px; height: 1200px; overflow: hidden;
    background: var(--canvas);
    font-family: "Open Sans", Arial, sans-serif;
  }
  .canvas {
    position: relative; width: 794px; height: 1200px;
  }
  .card {
    position: absolute; left: 87px; width: 620px; height: 354px;
    background: var(--paper); overflow: hidden;
    box-shadow: 0 6px 18px rgba(0,0,0,0.18);
  }
  .card--front { top: 190px; }
  .card--back { top: 656px; }

  .panel {
    position: absolute; top: 0; width: 270px; height: 100%;
  }
  .card--front .panel { right: 0; }
  .card--back .panel { left: 0; }
  .panel svg { display: block; width: 100%; height: 100%; }

  .identity { position: absolute; left: 44px; top: 48px; }
  .identity__name {
    font-size: 31px; font-weight: 400; color: var(--ink); letter-spacing: -0.3px;
  }
  .identity__title {
    font-size: 15px; font-weight: 600; color: var(--green-dark);
    margin-left: 42px; margin-top: -2px;
  }

  .accent-bar {
    position: absolute; left: 40px; top: 142px; width: 5px; height: 168px;
    background: var(--green);
  }
  .contacts { position: absolute; left: 62px; top: 146px; }
  .contacts__row {
    display: flex; font-size: 12.5px; line-height: 19px; color: var(--ink);
  }
  .contacts__label { width: 30px; }
  .contacts__sep { width: 16px; }
  .contacts__email { font-size: 12.5px; color: var(--ink); line-height: 20px; }
  .address {
    position: absolute; left: 62px; top: 262px;
    font-size: 10px; line-height: 15px; color: var(--ink-soft);
  }
  .web {
    position: absolute; right: 16px; bottom: 14px;
    font-size: 11px; color: var(--paper);
  }

  .brand {
    position: absolute; left: 360px; top: 155px;
    display: flex; align-items: center; gap: 10px;
  }
  .brand__mark { width: 26px; height: 26px; background: var(--green-dark); }
  .brand__name {
    font-size: 30px; font-weight: 700; color: var(--green); letter-spacing: -0.5px;
  }
</style>
</head>
<body>
<main class="canvas">

  <section class="card card--front" aria-label="Card front">
    <div class="identity">
      <h1 class="identity__name">Marcus Hale</h1>
      <p class="identity__title">director</p>
    </div>

    <div class="accent-bar"></div>

    <div class="contacts">
      <div class="contacts__row"><span class="contacts__label">tel</span><span class="contacts__sep">:</span><span>(555) 210 4410</span></div>
      <div class="contacts__row"><span class="contacts__label">cell</span><span class="contacts__sep">:</span><span>(555) 210 4411</span></div>
      <div class="contacts__row"><span class="contacts__label">fax</span><span class="contacts__sep">:</span><span>(555) 210 4412</span></div>
      <div class="contacts__email">office@restwavebeds.com</div>
    </div>

    <p class="address">410 Harbor Lane, Suite 12,<br>Riverton IL 60614</p>

    <div class="panel">
      <svg viewBox="0 0 270 354" preserveAspectRatio="none" aria-hidden="true">
        <rect width="270" height="354" fill="var(--green)"/>
        <polygon points="0,0 110,0 0,90" fill="var(--green-dark)"/>
        <polygon points="170,0 270,0 270,110" fill="var(--green-dark)"/>
        <rect x="0" y="265" width="70" height="89" fill="var(--green-dark)"/>
      </svg>
    </div>
    <p class="web">www.restwave-beds.com</p>
  </section>

  <section class="card card--back" aria-label="Card back">
    <div class="panel">
      <svg viewBox="0 0 270 354" preserveAspectRatio="none" aria-hidden="true">
        <rect width="270" height="354" fill="var(--green)"/>
        <polygon points="0,0 120,0 0,100" fill="var(--green-dark)"/>
        <polygon points="150,0 270,0 270,80" fill="var(--green-dark)"/>
        <rect x="200" y="270" width="70" height="84" fill="var(--green-dark)"/>
      </svg>
    </div>

    <div class="brand">
      <span class="brand__mark"></span>
      <span class="brand__name">Restwave</span>
    </div>
  </section>

</main>
</body>
</html>
```